Website design for Puddle Jump Kidscare

I need a website designed for my daycare business, Puddle Jump Kidscare, now that I have a new logo. My former website was ok but simple and I did not have a logo yet. It also was created by me using a template and was entirely pink. I loved the bright, happy feel of it but worried it might not appeal as much to potential clients who have sons. Therefore, I need a site which will appeal to both genders while still keeping the cheerful color scheme of my new logo, which has pinks, blue, green and cream.
Updates

Reason: Hello! I am still trying to download my new logo and am sorry it is taking me so long. Hopefully I will it posted by the end of today (US Eastern Standard Time). Thank you all very much for your patience!

Hello! I have finally managed to upload my new logo for you to use in designing my website. I'm sorry it took so long and greatly appreciate your time and creative efforts! I look forward to seeing what is submitted based on my logo design and its style/colors.

Many thanks!

Reason: As I've been traveling and posted my logo file late, I am extending my deadline. I am now back and can focus on providing more and better feedback. I appreciate your patience and submissions very much!

Reason: I need more time to provide feedback and make decisions.

Industry/Entity Type

Daycare

Colors
0192cd
33a6d7
86cae7
cadf82
fbf289
add136
e34197

```html
<!DOCTYPE html>
<html lang="en">
<head>
<meta charset="utf-8">
<title>Puddle Jump Kidscare</title>
<link href="https://fonts.googleapis.com/css2?family=Varela+Round&family=Lato:wght@700&family=Open+Sans:ital,wght@0,400;0,600;1,400;1,600&display=swap" rel="stylesheet">
<style>
:root{
  --sky-top:#2a5f98;
  --sky-mid:#3a82c0;
  --cream:#f2eeea;
  --pink:#f08bc8;
  --pink-deep:#e5659f;
  --green:#6aa51d;
  --blue:#3f8ccc;
  --rose:#ea7cc4;
  --ink:#2b2b2b;
  --body:#4a4a4a;
  --link:#2596c9;
  --grey:#6c6c6c;
  --line:#dcd7d2;
  --white:#ffffff;
}
*{margin:0;padding:0;box-sizing:border-box}
html,body{width:1012px;height:1200px;overflow:hidden}
body{
  position:relative;
  font-family:"Open Sans",sans-serif;
  color:var(--body);
  background:linear-gradient(180deg,var(--sky-top) 0,var(--sky-mid) 220px,#5b8fc2 290px,var(--cream) 350px,var(--cream) 100%);
}
.brand{position:absolute;left:148px;top:30px;display:flex;align-items:center;gap:12px}
.brand-dot{width:34px;height:34px;border-radius:50%;background:var(--pink)}
.brand-name{font-family:"Varela Round",sans-serif;font-size:27px;color:var(--white)}
.social{position:absolute;left:770px;top:42px;display:flex;gap:6px}
.social span{width:20px;height:20px;border-radius:50%;background:#4b4f55;border:2px solid #7d8187}
.nav{position:absolute;left:145px;top:99px;width:722px;height:45px;background:var(--pink);display:flex;list-style:none;border-radius:2px 2px 0 0}
.nav li{font-family:"Lato",sans-serif;font-size:10.5px;color:var(--white);display:flex;align-items:center;justify-content:center;border-right:1px solid #f6a9d6;flex:auto}
.nav li:last-child{border-right:none}
.slider{position:absolute;left:144px;top:144px;width:723px;height:347px;background:var(--white);border:1px solid #e2dedb}
.slider-photo{position:absolute;left:6px;top:5px;width:711px;height:336px;background:linear-gradient(180deg,#e9e6e1 0,#d9c9b5 45%,#d84a3c 78%,#f2c419 100%)}
.arrow{position:absolute;top:193px;width:36px;height:41px;background:rgba(255,255,255,.55);display:flex;align-items:center;justify-content:center}
.arrow.prev{left:6px}.arrow.next{right:6px}
.feature{position:absolute;top:516px;width:231px;height:262px;color:var(--white);text-align:center}
.feature svg.top{position:absolute;left:0;top:0}
.feature .panel{position:absolute;left:0;top:22px;width:231px;height:240px;border-radius:0 0 3px 3px}
.feature .badge{position:absolute;left:65px;top:36px;width:102px;height:102px;border-radius:50%;background:#f6f1ec;box-shadow:0 3px 6px rgba(0,0,0,.2);display:flex;align-items:center;justify-content:center}
.feature .badge span{width:62px;height:54px;border-radius:8px}
.feature h3{position:absolute;left:0;right:0;top:153px;font-weight:600;font-style:italic;font-size:13px;letter-spacing:.3px}
.feature p{position:absolute;left:20px;right:20px;top:182px;font-size:8.8px;line-height:16px;font-style:italic;font-weight:600}
.learning{left:145px}.learning .panel{background:var(--green)}
.creativity{left:390px}.creativity .panel{background:var(--blue)}
.sharing{left:636px}.sharing .panel{background:var(--rose)}
.col{position:absolute;top:808px;width:222px}
.col h2{font-weight:400;font-size:13.5px;color:var(--ink);height:34px;line-height:20px}
.col h2 em{color:var(--pink-deep);font-weight:600}
.welcome{left:144px}
.welcome-photo{width:222px;height:127px;border:1px solid #ddd;background:linear-gradient(180deg,#f4efe6 0,#e9d8c0 40%,#f2d02a 75%,#43b56a 100%)}
.welcome p{margin-top:20px;font-size:8.9px;line-height:16px;text-align:justify}
.readmore{margin-top:20px;font-size:8.9px;color:var(--ink);display:flex;align-items:center;gap:6px}
.readmore i{width:6px;height:6px;border-radius:50%;border:1.5px solid #f39a1e}
.services{left:399px}
.services h2{border-bottom:1px solid var(--line);height:34px;margin-top:3px}
.services p{margin-top:10px;font-size:8.9px;line-height:16px;text-align:justify;color:var(--ink)}
.services ul{list-style:none;margin-top:29px}
.services li{font-size:8.9px;color:var(--link);height:37px;line-height:22px;border-bottom:1px solid var(--line);padding-left:15px;position:relative;margin-top:-10px;padding-top:3px}
.services li:first-child{margin-top:-12px}
.services li::before{content:"›";position:absolute;left:0;top:3px;color:#777}
.news{left:657px;width:212px}
.news h2{border-bottom:1px solid #e6e1dc}
.event{position:absolute;left:2px;width:210px}
.date{position:absolute;left:0;top:0;width:40px}
.date .day{height:54px;background:var(--pink);color:var(--white);text-align:center;font-family:"Varela Round",sans-serif;position:relative}
.date .day b{display:block;font-weight:400;font-size:16px;padding-top:9px}
.date .day small{display:block;font-size:10px;margin-top:6px}
.date .day::after{content:"";position:absolute;right:-7px;top:8px;border-left:7px solid var(--pink);border-top:7px solid transparent;border-bottom:7px solid transparent}
.date .talk{height:23px;background:var(--grey);display:flex;align-items:center;justify-content:center}
.event h4{position:absolute;left:59px;top:5px;font-weight:400;font-size:13.5px;color:var(--ink);white-space:nowrap}
.event p{position:absolute;left:59px;top:36px;width:152px;font-size:8.9px;line-height:16px;text-align:justify}
.footer{position:absolute;left:0;top:1146px;width:1012px;height:54px;border-top:1px solid #e2ddd8;background:#f5f2ef}
.footer nav{position:absolute;left:143px;top:22px;font-size:9.4px;color:#444;letter-spacing:.3px;word-spacing:2px}
.footer .copy{position:absolute;right:144px;top:22px;font-size:9.4px;color:#555;letter-spacing:.3px}
</style>
</head>
<body>
<header>
  <div class="brand"><span class="brand-dot"></span><span class="brand-name">Puddle Jump Kidscare</span></div>
  <div class="social" aria-label="Social links"><span></span><span></span><span></span><span></span></div>
  <ul class="nav">
    <li>HOME</li><li>ABOUT</li><li>SERVICES</li><li>HOURS AND FEES</li><li>POLICIES</li><li>PHOTOS</li><li>TESTIMONIALS</li><li>CONTACT US</li>
  </ul>
</header>

<section class="slider">
  <div class="slider-photo" role="img" aria-label="Photo of a teacher painting with children at a classroom table"></div>
  <div class="arrow prev"><svg width="10" height="14" viewBox="0 0 10 14"><path d="M8 1 2 7l6 6" fill="none" stroke="#333" stroke-width="2.5"/></svg></div>
  <div class="arrow next"><svg width="10" height="14" viewBox="0 0 10 14"><path d="M2 1l6 6-6 6" fill="none" stroke="#333" stroke-width="2.5"/></svg></div>
</section>

<section class="feature learning">
  <svg class="top" width="231" height="30" viewBox="0 0 231 30"><path d="M0 30V18Q0 8 25 4Q60 -2 95 4Q125 0 150 8Q170 12 190 12Q210 12 225 16Q231 18 231 24V30Z" fill="#6aa51d"/></svg>
  <div class="panel"></div>
  <div class="badge"><span role="img" aria-label="Illustration of a stack of books with an apple" style="background:linear-gradient(180deg,#d8322a 0,#e8d7a3 45%,#4c8a3a 100%)"></span></div>
  <h3>LEARNING</h3>
  <p>We develop age-appropriate activities that intro-duce and strengthen academic and social skills.We develop age-appropriate activities that introduce and strengthen</p>
</section>

<section class="feature creativity">
  <svg class="top" width="231" height="30" viewBox="0 0 231 30"><path d="M0 30V18Q0 8 20 6Q45 -2 75 4Q110 -2 140 6Q175 4 205 12Q231 14 231 24V30Z" fill="#3f8ccc"/></svg>
  <div class="panel"></div>
  <div class="badge"><span role="img" aria-label="Illustration of a paint palette and brush" style="background:linear-gradient(135deg,#d9a35a 0,#c9873c 60%,#3b7fc4 100%)"></span></div>
  <h3>CREATIVITY</h3>
  <p>We offer children a wide range of creative oppor-tunities including art projects, toddler yoga lessons, afternoon tea parties, dress up play, and a large selection of books and games.</p>
</section>

<section class="feature sharing">
  <svg class="top" width="231" height="30" viewBox="0 0 231 30"><path d="M0 30V18Q0 8 30 4Q70 -2 110 4Q150 -2 190 2Q231 6 231 24V30Z" fill="#ea7cc4"/></svg>
  <div class="panel"></div>
  <div class="badge"><span role="img" aria-label="Illustration of coloured pencils arranged in a circle" style="border-radius:50%;width:70px;height:70px;background:conic-gradient(#e8453c,#f29a2e,#f4d23a,#5dbb46,#2e8fd0,#8a4fb8,#e8453c)"></span></div>
  <h3>SHARING</h3>
  <p>We develop age-appropriate activities that intro-duce and strengthen academic and social skills.We develop age-appropriate activities that introduce and strengthen</p>
</section>

<section class="col welcome">
  <h2>Welcome to <em>Puddle Jump Kidscare</em></h2>
  <div class="welcome-photo" role="img" aria-label="Photo of four smiling children standing together"></div>
  <p>Welcome to Puddle Jump Kidscare, a licensed Group Family Day Care, located in Harbor City's beautiful Upper Brookside. We are located on a pretty, tree-lined block on Linden Street, between Elm and Oak Avenues. We are a few blocks from the Green Line tram and the Maple Road bus route, and we offer flexible</p>
  <div class="readmore">Read more <i></i></div>
</section>

<section class="col services">
  <h2>Services We Provide</h2>
  <p>Lorem ipsum dolor sit amet, consectetuer adipiscing elit, sed diam nonummy nibh euismod tincidunt ut laoreet dolore magna aliquam erat volutpat. Ut wisi enim ad minim veniam.</p>
  <ul>
    <li>Flexible hourly full and part-time childcare</li>
    <li>Discount for siblings</li>
    <li>Small adult: child ratio</li>
    <li>Daily schedules that vary per the age of children</li>
    <li>Large selection of books</li>
  </ul>
</section>

<section class="col news">
  <h2>News &amp; Events</h2>
  <article class="event" style="top:48px">
    <div class="date"><div class="day"><b>15</b><small>OCT</small></div><div class="talk"><svg width="13" height="11" viewBox="0 0 13 11"><ellipse cx="6.5" cy="4.5" rx="6" ry="4.2" fill="#fff"/><path d="M3 7 1.5 10.5 6 8z" fill="#fff"/></svg></div></div>
    <h4>Morbi tempor quam</h4>
    <p>Morbi tempor quam vel massa adi piscing ute cursus mi congue pelle ntesque niselit er comte</p>
  </article>
  <article class="event" style="top:138px">
    <div class="date"><div class="day"><b>15</b><small>OCT</small></div><div class="talk"><svg width="13" height="11" viewBox="0 0 13 11"><ellipse cx="6.5" cy="4.5" rx="6" ry="4.2" fill="#fff"/><path d="M3 7 1.5 10.5 6 8z" fill="#fff"/></svg></div></div>
    <h4>Set ipsum dolor sit amet</h4>
    <p>Morbi tempor quam vel massa adi piscing ute cursus mi congue pelle ntesque niselit er comte</p>
  </article>
  <article class="event" style="top:227px">
    <div class="date"><div class="day"><b>15</b><small>OCT</small></div><div class="talk"><svg width="13" height="11" viewBox="0 0 13 11"><ellipse cx="6.5" cy="4.5" rx="6" ry="4.2" fill="#fff"/><path d="M3 7 1.5 10.5 6 8z" fill="#fff"/></svg></div></div>
    <h4>Magna dolor sit amet</h4>
    <p>Morbi tempor quam vel massa adi piscing ute cursus mi congue pelle ntesque niselit er comte</p>
  </article>
</section>

<footer class="footer">
  <nav>HOME &nbsp;&nbsp;| &nbsp;&nbsp;ABOUT US &nbsp;&nbsp;| &nbsp;&nbsp;SERVICES | &nbsp;HOURS AND FEES &nbsp;| &nbsp;CONTACT US</nav>
  <div class="copy">©2014 2014 &nbsp;PUDDLE JUMP KIDSCARE, ALL RIGHTS RESERVED.</div>
</footer>
</body>
</html>
```